Thornvale Group needs a business card design

We need a new business card design using the logo recently selected in a logo competition on Pixel Bazaar. Our business is a consultancy specializing in aviation and energy and the winning business card design will promote an image of precision and professionalism with creativity.

Please use the logo with the name on the front of the card and use a complementary font. Make the back white with either the light grey or dark grey logo.

Target Market(s)

Senior finance and legal leaders at aviation and energy companies

Industry/Entity Type

Management Consulting

Contact Information for Business Card

Peter Castrell
President
Thornvale Group

www.thornvalegroup.example

(555) 204-6391
pc@thornvalegroup.example

Requirements
Must have
• Professional font that goes well with the logo font

```html
<!DOCTYPE html>
<html lang="en">
<head>
<meta charset="utf-8">
<title>Thornvale Group – Business Card</title>
<link href="https://fonts.googleapis.com/css2?family=Libre+Franklin:ital,wght@0,400;0,600;1,400&display=swap" rel="stylesheet">
<style>
  :root {
    --page: #e9e7e3;
    --card: #ffffff;
    --card-shade: #e6e6e6;
    --navy: #0b3d6e;
    --slate: #5a5c60;
    --ink: #3b3d41;
    --muted: #6f7175;
    --text-font: "Libre Franklin", Arial, sans-serif;
  }
  * { box-sizing: border-box; margin: 0; padding: 0; }
  html, body {
    width: 1200px; height: 950px; overflow: hidden;
    background: var(--page);
    font-family: var(--text-font);
  }
  .sheet {
    width: 1200px; height: 950px;
    display: flex; flex-direction: column; align-items: center;
    justify-content: space-evenly;
  }
  .card {
    position: relative;
    width: 700px; height: 400px;
    background: linear-gradient(160deg, var(--card) 0%, var(--card) 55%, var(--card-shade) 100%);
    box-shadow: 0 6px 18px rgba(0,0,0,.18);
    overflow: hidden;
  }

  /* Brand name: plain text with one square marker */
  .brand {
    display: flex; align-items: center; gap: 14px;
    color: var(--navy);
    font-weight: 400;
    line-height: 1;
    white-space: nowrap;
  }
  .brand-square {
    flex: none;
    background: var(--navy);
  }

  /* Front */
  .brand-front {
    position: absolute; left: 44px; top: 58px;
    font-size: 36px;
  }
  .brand-front .brand-square { width: 26px; height: 26px; }

  .bands { position: absolute; left: 0; top: 0; }

  .person {
    position: absolute; left: 44px; top: 158px; color: #fff;
  }
  .person .full-name { font-size: 22px; font-weight: 600; letter-spacing: .3px; }
  .person .role { font-size: 15px; font-style: italic; margin-top: 2px; }

  .contact {
    position: absolute; left: 40px; top: 236px;
    list-style: none; color: var(--ink); font-size: 15px;
  }
  .contact li { display: flex; align-items: center; gap: 8px; height: 22px; }
  .contact svg { width: 14px; height: 14px; flex: none; }

  .company-lines {
    position: absolute; right: 40px; top: 286px;
    text-align: right; color: var(--muted); font-size: 16px; line-height: 1.3;
  }

  /* Back */
  .back-center {
    position: absolute; inset: 0;
    display: flex; align-items: center; justify-content: center;
  }
  .brand-back { font-size: 44px; gap: 18px; }
  .brand-back .brand-square { width: 32px; height: 32px; }
</style>
</head>
<body>
<main class="sheet">

  <section class="card card-front" aria-label="Business card front">
    <div class="brand brand-front">
      <span class="brand-square" aria-hidden="true"></span>
      <span class="brand-name">Thornvale Group</span>
    </div>

    <svg class="bands" width="700" height="400" viewBox="0 0 700 400" aria-hidden="true">
      <polygon class="band-navy" points="0,150 500,150 455,212 0,212" fill="var(--navy)"/>
      <polygon class="band-slate" points="500,212 700,212 700,268 460,268" fill="var(--slate)"/>
    </svg>

    <div class="person">
      <p class="full-name">Peter Castrell</p>
      <p class="role">President</p>
    </div>

    <ul class="contact">
      <li>
        <svg viewBox="0 0 14 14"><circle cx="7" cy="7" r="7" fill="var(--ink)"/><path d="M4.3 3.6h1.6l.6 1.8-.9.7a5 5 0 0 0 2.3 2.3l.7-.9 1.8.6v1.6a.8.8 0 0 1-.9.7A6.2 6.2 0 0 1 3.6 4.5a.8.8 0 0 1 .7-.9z" fill="#fff"/></svg>
        (555) 204-6391
      </li>
      <li>
        <svg viewBox="0 0 14 14"><rect x="1" y="3" width="12" height="8" fill="var(--ink)"/><path d="M1.5 3.5 7 8l5.5-4.5" fill="none" stroke="#fff" stroke-width="1"/></svg>
        pc@thornvalegroup.example
      </li>
      <li>
        <svg viewBox="0 0 14 14"><circle cx="7" cy="7" r="6.5" fill="var(--ink)"/><path d="M.8 7h12.4M7 .8c-3 3.4-3 9 0 12.4M7 .8c3 3.4 3 9 0 12.4" fill="none" stroke="#fff" stroke-width=".9"/></svg>
        thornvalegroup.example
      </li>
    </ul>

    <div class="company-lines">
      <p>Thornvale Group LLC</p>
      <p>Finance and Strategy Consulting</p>
      <p>Aviation - Manufacturing - Energy</p>
    </div>
  </section>

  <section class="card card-back" aria-label="Business card back">
    <div class="back-center">
      <div class="brand brand-back">
        <span class="brand-square" aria-hidden="true"></span>
        <span class="brand-name">Thornvale Group</span>
      </div>
    </div>
  </section>

</main>
</body>
</html>
```